Veltrona Limited Business Card Design Project

Veltrona Limited is my UK based company used as my brand to work as an Interim Manager or contractor in project/programme management and Non-Executive Director.

Veltrona is Latin for 'execute' as in getting things done rather than killing people!

Logo and design needs to promote reliable, professional, and successful project delivery. Simple, elegant, clean, professional are words that should spring to mind!

Target Market(s)

Middle and senior management in english speaking countries aged 35 - 60 that hire and task qualified and experienced project/programme managers and Non-Executive Directors.

Industry/Entity Type

Contractor

Font styles to use
Serif
Sans Serif

Requirements
Must have
• Mobile telephone number 07842 615098
email address marcusholloway@veltrona.co.uk
Nice to have
• LinkedIn link to my profile.

Interim Manager
Should not have
• avoid Ticks and clocks

```html
<!DOCTYPE html>
<html lang="en">
<head>
<meta charset="utf-8">
<title>Veltrona Limited – Business Card Front and Back</title>
<link rel="stylesheet" href="https://fonts.googleapis.com/css2?family=Oswald:wght@400;500&family=Lato:ital,wght@0,400;0,700;0,900;1,700&display=swap">
<style>
  :root {
    --page-bg: #dcdde0;
    --blue-light: #1f87c9;
    --blue-dark: #0b67b2;
    --blue-rule: #4fa5dc;
    --stripe-pale: #bfe4f9;
    --stripe-soft: #8fcdf2;
    --panel-top: #ffffff;
    --panel-bottom: #d9dadc;
    --ink-dark: #2b2b2b;
    --ink-mid: #4a4a4a;
    --ink-blue: #1a7fc4;
    --white: #ffffff;
    --back-bg: #2f2e2f;
    --back-band: #59595b;
    --back-band-light: #6c6c6e;
  }
  * { box-sizing: border-box; margin: 0; padding: 0; }
  html, body { width: 1000px; height: 1200px; overflow: hidden; }
  body {
    background: var(--page-bg);
    font-family: "Lato", Arial, sans-serif;
    position: relative;
  }
  .card {
    position: absolute;
    left: 70px;
    width: 860px;
    height: 518px;
    overflow: hidden;
    box-shadow: 0 6px 18px rgba(0,0,0,0.25);
  }
  .card--front { top: 57px; background: var(--blue-light); }
  .card--back { top: 625px; background: var(--back-bg); }

  .band { position: absolute; left: 0; width: 100%; }
  .band--name { top: 96px; height: 111px; background: var(--blue-dark); border-top: 2px solid var(--blue-rule); }
  .band--stripes {
    top: 207px; height: 105px;
    background: linear-gradient(90deg, var(--stripe-soft), var(--stripe-pale) 50%, var(--stripe-soft));
    border-top: 2px solid var(--white);
    border-bottom: 2px solid var(--white);
  }
  .band--social { top: 312px; height: 109px; background: var(--blue-dark); border-bottom: 2px solid var(--blue-rule); }

  .holder { position: absolute; left: 62px; top: 126px; color: var(--white); }
  .holder__name { font-family: "Oswald", Arial, sans-serif; font-weight: 500; font-size: 30px; line-height: 1; text-transform: uppercase; }
  .holder__role { font-weight: 700; font-size: 15px; text-transform: uppercase; margin-top: 5px; }

  .social { position: absolute; left: 62px; top: 340px; list-style: none; color: var(--white); }
  .social__item { display: flex; align-items: center; font-weight: 700; font-style: italic; font-size: 17px; height: 33px; }
  .social__dot { width: 20px; height: 20px; border-radius: 50%; background: var(--white); margin-right: 9px; }

  .panel { position: absolute; left: 365px; top: 65px; width: 430px; height: 383px; }
  .panel svg { position: absolute; left: 0; top: 0; }
  .panel__body { position: absolute; left: 52px; top: 48px; right: 20px; }
  .panel__company { font-weight: 700; font-size: 35px; color: var(--ink-dark); line-height: 1; white-space: nowrap; }
  .panel__slogan { font-size: 14px; letter-spacing: 5px; color: var(--ink-mid); margin-top: 9px; white-space: nowrap; }
  .panel__brand { font-family: "Oswald", Arial, sans-serif; font-size: 31px; text-transform: uppercase; margin-top: 80px; line-height: 1; color: var(--ink-dark); }
  .panel__brand-accent { color: var(--ink-blue); }
  .panel__contact { list-style: none; margin-top: 14px; font-size: 16px; color: var(--ink-mid); line-height: 23px; white-space: nowrap; }

  .back-band {
    position: absolute; left: 0; top: 207px; width: 100%; height: 105px;
    background: linear-gradient(90deg, var(--back-band), var(--back-band-light) 60%, var(--back-band));
  }
  .back-text { position: absolute; left: 58px; top: 222px; color: var(--white); }
  .back-text__brand { font-family: "Oswald", Arial, sans-serif; font-size: 44px; line-height: 1; text-transform: uppercase; }
  .back-text__site { font-weight: 900; font-size: 19px; letter-spacing: 1px; margin-top: 4px; text-transform: uppercase; }
</style>
</head>
<body>
  <section class="card card--front" aria-label="Business card front">
    <div class="band band--name"></div>
    <div class="band band--stripes" role="img" aria-label="Pale blue diagonal stripe band"></div>
    <div class="band band--social"></div>

    <div class="holder">
      <p class="holder__name">Marcus Holloway</p>
      <p class="holder__role">Interim Manager</p>
    </div>

    <ul class="social">
      <li class="social__item"><span class="social__dot"></span>sn.me/veltrona</li>
      <li class="social__item"><span class="social__dot"></span>@veltrona</li>
    </ul>

    <div class="panel">
      <svg width="430" height="383" viewBox="0 0 430 383" aria-hidden="true">
        <defs>
          <linearGradient id="panel-fill" x1="0" y1="0" x2="0" y2="1">
            <stop offset="0" stop-color="var(--panel-top)"/>
            <stop offset="1" stop-color="var(--panel-bottom)"/>
          </linearGradient>
        </defs>
        <path d="M32 0 H416 Q430 0 430 14 V369 Q430 383 416 383 H32 Q18 383 18 369 V108 L0 86 L18 64 V14 Q18 0 32 0 Z"
              fill="url(#panel-fill)" stroke="#a9abae" stroke-width="1.5"/>
      </svg>
      <div class="panel__body">
        <p class="panel__company">Veltrona Limited</p>
        <p class="panel__slogan">Getting Things Done</p>
        <p class="panel__brand"><span class="panel__brand-accent">Veltrona</span> Limited</p>
        <ul class="panel__contact">
          <li>14 Harbour Street, Bristol BS1 4QA</li>
          <li>07842 615098</li>
          <li>marcusholloway@veltrona.co.uk</li>
          <li>www.veltrona.co.uk</li>
        </ul>
      </div>
    </div>
  </section>

  <section class="card card--back" aria-label="Business card back">
    <div class="back-band" role="img" aria-label="Grey diagonal stripe band"></div>
    <div class="back-text">
      <p class="back-text__brand">Veltrona Limited</p>
      <p class="back-text__site">www.veltrona.co.uk</p>
    </div>
  </section>
</body>
</html>
```